Copperleaf Roofing Business Card

This is my current business card. But I’d like to make some changes. Somewhere on the card I’d like to list some of the services we offer. Maybe on the back? But I’d still like to keep the red. White and black modern look.

-residential & commercial roofing
-Roof Repairs & Maintenance
-Storm Damage & Insurance Claims specialist
-Christmas Lights and permanent Christmas lights
Fencing. Windows. Gutters. Siding. Sheetrock, painting.

```html
<!DOCTYPE html>
<html lang="en">
<head>
<meta charset="utf-8">
<title>Copperleaf Roofing Co. – Business Card</title>
<link href="https://fonts.googleapis.com/css2?family=Michroma&family=Lato:wght@400;700&display=swap" rel="stylesheet">
<style>
  :root {
    --stage: #3a3a3a;
    --red: #e01e24;
    --red-deep: #8e1116;
    --black: #111111;
    --white: #ffffff;
    --ink: #1a1a1a;
    --rule: #2b2b2b;
  }
  * { margin: 0; padding: 0; box-sizing: border-box; }
  html, body { width: 1200px; height: 694px; overflow: hidden; }
  body {
    background: var(--stage);
    font-family: "Lato", Arial, sans-serif;
    position: relative;
  }
  .card {
    position: absolute;
    top: 187px;
    width: 560px;
    height: 320px;
    border-radius: 18px;
    overflow: hidden;
  }
  .card--front { left: 30px; background: var(--red); }
  .card--back { left: 610px; background: var(--white); }

  .tartan-fill {
    position: absolute; inset: 0;
    background: linear-gradient(135deg, var(--red-deep) 0%, var(--red) 35%, var(--black) 60%, var(--red) 80%, var(--red-deep) 100%);
  }
  .front-brand {
    position: absolute; left: 0; right: 0; top: 58px;
    display: flex; flex-direction: column; align-items: center; gap: 14px;
  }
  .brand-dot {
    width: 96px; height: 96px; border-radius: 50%;
    background: var(--black); border: 4px solid var(--white);
  }
  .brand-name {
    font-family: "Michroma", Arial, sans-serif;
    font-size: 24px; letter-spacing: 1px; line-height: 1.2;
    text-align: center; color: var(--white);
  }
  .services {
    position: absolute; left: 30px; right: 30px; bottom: 26px;
    list-style: none; text-align: center;
    color: var(--white); font-weight: 700; font-size: 12.5px; line-height: 1.55;
  }
  .services li { display: inline; }
  .services li::before { content: "• "; }
  .services li + li { margin-left: 6px; }

  .back-brand {
    position: absolute; right: 34px; top: 34px;
    display: flex; align-items: center; gap: 14px;
  }
  .back-brand .brand-dot { width: 64px; height: 64px; border: 0; background: var(--red); }
  .back-brand .brand-name { color: var(--black); font-size: 20px; text-align: left; }
  .divider {
    position: absolute; left: 200px; right: 34px; top: 140px;
    height: 1px; background: var(--rule);
  }
  .accent-bar {
    position: absolute; left: 0; top: 190px; width: 8px; height: 46px; background: var(--red);
  }
  .holder { position: absolute; left: 34px; top: 190px; }
  .holder-name {
    font-family: "Michroma", Arial, sans-serif;
    color: var(--red); font-size: 22px; letter-spacing: 1px;
  }
  .holder-role { color: var(--ink); font-size: 15px; margin-top: 2px; }
  .holder-rule {
    position: absolute; left: 34px; width: 260px; top: 246px; height: 1px; background: var(--rule);
  }
  .contacts {
    position: absolute; left: 34px; top: 256px; list-style: none;
    color: var(--ink); font-size: 13.5px; line-height: 20px;
  }
  .contacts li { display: flex; align-items: center; gap: 10px; }
  .contacts svg { width: 14px; height: 14px; fill: var(--red); }
</style>
</head>
<body>

<section class="card card--front" aria-label="Card front">
  <div class="tartan-fill" role="img" aria-label="Red, white and black tartan plaid pattern"></div>
  <div class="front-brand">
    <div class="brand-dot"></div>
    <div class="brand-name">COPPERLEAF<br>ROOFING CO.</div>
  </div>
  <ul class="services">
    <li>Residential &amp; commercial roofing</li>
    <li>Roof Repairs &amp; Maintenance</li>
    <li>Storm Damage &amp; Insurance Claims specialist</li>
    <li>Christmas Lights and permanent Christmas light</li>
    <li>Fencing</li><li>Windows</li><li>Siding</li><li>Sheetrock</li><li>Painting</li>
  </ul>
</section>

<section class="card card--back" aria-label="Card back">
  <div class="back-brand">
    <div class="brand-dot"></div>
    <div class="brand-name">COPPERLEAF<br>ROOFING CO.</div>
  </div>
  <div class="divider"></div>
  <div class="accent-bar"></div>
  <div class="holder">
    <div class="holder-name">DALE MERCER</div>
    <div class="holder-role">Owner</div>
  </div>
  <div class="holder-rule"></div>
  <ul class="contacts">
    <li>
      <svg viewBox="0 0 24 24" aria-hidden="true"><path d="M6.6 10.8a15 15 0 0 0 6.6 6.6l2.2-2.2a1 1 0 0 1 1-.25 11.4 11.4 0 0 0 3.6.57 1 1 0 0 1 1 1V20a1 1 0 0 1-1 1A17 17 0 0 1 3 4a1 1 0 0 1 1-1h3.5a1 1 0 0 1 1 1c0 1.25.2 2.45.57 3.57a1 1 0 0 1-.25 1z"/></svg>
      555-014-2287
    </li>
    <li>
      <svg viewBox="0 0 24 24" aria-hidden="true"><path d="M2 5h20v14H2zM4 7v.5l8 5 8-5V7l-8 5z"/></svg>
      Dale@copperleafroofing.co
    </li>
    <li>
      <svg viewBox="0 0 24 24" aria-hidden="true"><circle cx="12" cy="12" r="10"/></svg>
      www.copperleafroofing.co
    </li>
  </ul>
</section>

</body>
</html>
```